Lunelle Rosa Hair Fancy Business Card’s

I want my business cards to be elite, original and very classy. I want the business cards to match the colors of my logo and to match the design posted. I would love the design of the picture I posted

I want the card all white .
The dripping on the top of the card I want it to match the pink color in my logo that’s also posted .
I need my logo on the business card !
I need my Instagram- @lunelle.rosa.hair__
And my phone number - 555 207 3962

Target Market(s)

My target market is young woman age 23 to older woman to the age of 65
I want both older and younger women to love my design . I don’t want any cheap looking business cards

Industry/Entity Type

Hair And Beauty

Contact Information for Business Card

Add my logo
Add my Instagram- @lunelle.rosa.hair__
My number - 555 207 3962
My website- www.lunellerosahair.example

Font styles to use
Serif
Script

Colors
ffffff
e667a6
e34298

Requirements
Must have
• The business cards must have my logo, my number , my website, and my Instagram!
Nice to have
• Nice to have glitter words that match my logo
• The business cards must look classy and mature
• I want them to be very unique!!
Should not have
• Should not have any colors that doesn’t match my logo ! This is very important! Please

```html
<!DOCTYPE html>
<html lang="en">
<head>
<meta charset="utf-8">
<title>Lunelle Rosa Hair – Business Card</title>
<link rel="stylesheet" href="https://fonts.googleapis.com/css2?family=Montserrat:wght@400;500&family=Great+Vibes&display=swap">
<style>
  :root {
    --stage: #e9e7e4;
    --card-dark: #262626;
    --card-light: #ffffff;
    --pink: #b8438f;
    --grey: #55554f;
    --ink: #3a3a3a;
  }
  * { margin: 0; padding: 0; box-sizing: border-box; }
  html, body { width: 1200px; height: 985px; overflow: hidden; }
  body {
    background: var(--stage);
    font-family: "Montserrat", sans-serif;
    display: flex;
    flex-direction: column;
    align-items: center;
    justify-content: center;
    gap: 36px;
  }
  .card {
    position: relative;
    width: 840px;
    height: 440px;
    box-shadow: 0 6px 18px rgba(0,0,0,0.18);
    overflow: hidden;
  }
  .card--front { background: var(--card-dark); display: flex; align-items: center; justify-content: center; }
  .card--back { background: var(--card-light); }

  .brand-name {
    font-family: "Montserrat", sans-serif;
    font-weight: 500;
    color: var(--pink);
    letter-spacing: 0.04em;
    text-transform: uppercase;
    line-height: 1.15;
  }
  .card--front .brand-name { font-size: 50px; text-align: center; }

  .back-layout {
    position: absolute;
    top: 70px;
    left: 0;
    width: 100%;
    display: flex;
    align-items: center;
  }
  .back-logo {
    width: 390px;
    display: flex;
    justify-content: flex-end;
    padding-right: 40px;
  }
  .back-logo .brand-name { font-size: 30px; text-align: right; }
  .divider { width: 2px; height: 190px; background: var(--ink); }
  .contact { padding-left: 42px; }
  .person-name {
    font-family: "Great Vibes", cursive;
    color: var(--pink);
    font-size: 46px;
    line-height: 1;
  }
  .person-role { font-size: 19px; color: var(--ink); margin: 4px 0 18px; }
  .contact-list { list-style: none; }
  .contact-list li {
    display: flex;
    align-items: center;
    gap: 12px;
    font-size: 21px;
    color: var(--ink);
    line-height: 1.5;
  }
  .contact-list .accent { color: var(--pink); }
  .icon { width: 18px; height: 18px; flex: none; }
  .wave { position: absolute; left: 0; bottom: 0; width: 840px; height: 440px; }
</style>
</head>
<body>
  <section class="card card--front" aria-label="Card front">
    <p class="brand-name">Lunelle Rosa<br>Hair</p>
  </section>

  <section class="card card--back" aria-label="Card back">
    <svg class="wave" viewBox="0 0 840 440" aria-hidden="true">
      <path fill="var(--grey)" d="M0 300 C150 298 260 325 340 360 C250 330 140 314 0 314 Z"/>
      <path fill="var(--pink)" d="M0 322 C220 334 420 432 640 426 C740 423 800 416 840 412 L840 440 L0 440 Z"/>
      <path fill="var(--grey)" d="M560 392 C680 408 780 404 840 397 L840 405 C780 412 680 414 560 392 Z"/>
    </svg>

    <div class="back-layout">
      <div class="back-logo">
        <p class="brand-name">Lunelle Rosa<br>Hair</p>
      </div>
      <div class="divider"></div>
      <div class="contact">
        <p class="person-name">Maren Holt</p>
        <p class="person-role">Manager</p>
        <ul class="contact-list">
          <li>
            <svg class="icon" viewBox="0 0 24 24" aria-hidden="true"><path fill="var(--pink)" d="M6.6 10.8a15.1 15.1 0 0 0 6.6 6.6l2.2-2.2a1 1 0 0 1 1-.25 11.4 11.4 0 0 0 3.6.57 1 1 0 0 1 1 1V20a1 1 0 0 1-1 1A17 17 0 0 1 3 4a1 1 0 0 1 1-1h3.5a1 1 0 0 1 1 1c0 1.25.2 2.45.57 3.57a1 1 0 0 1-.25 1z"/></svg>
            555 207 3962
          </li>
          <li>
            <svg class="icon" viewBox="0 0 24 24" aria-hidden="true"><rect x="3" y="3" width="18" height="18" rx="3" fill="var(--pink)"/></svg>
            @lunelle.rosa.hair__
          </li>
          <li>
            <svg class="icon" viewBox="0 0 24 24" aria-hidden="true"><circle cx="12" cy="12" r="9" fill="var(--pink)"/></svg>
            <span>www.<span class="accent">lunellerosahair</span>.example</span>
          </li>
        </ul>
      </div>
    </div>
  </section>
</body>
</html>
```